Banner for promote service of debit card

We are PagoLume and we need the banners to be posted on the facebook and instagram pages.
We want something to communicate that it is an exclusive debit card full of services.
Low commissions.
Our competitors:
https://www.kelmora.example/it/home.html
https://www.zofe.example/it/
https://www.socialpage.example/ostrevabank/
monadrift
maybe some banner that makes the idea of a convenient debit card that everyone can use.
Girls enjoying card shopping.
Please check also website for slogans and phrases to use
https://www.pagolume.example/
Should show the services.
We must convey that it is a fast, simple card that guarantees privacy.
We need strong banners that attract people as these ban will be sponsored on instagram and facebook
People 18-35 y
Open Bank account. low commissions. Easy to use. No limits. 100% Privacy.
- Written in Italian.

```html
<!DOCTYPE html>
<html lang="it">
<head>
<meta charset="utf-8">
<title>PagoLume – All in One</title>
<link rel="stylesheet" href="https://fonts.googleapis.com/css2?family=Montserrat:wght@600;700&family=Open+Sans:wght@400;600&display=swap">
<style>
  :root {
    --page-bg: #ffffff;
    --photo-dark: #1a100c;
    --photo-deep: #3a2216;
    --photo-mid: #6b3d22;
    --photo-warm: #b8703f;
    --photo-glow: #f0b67a;
    --text-light: #ffffff;
    --card-black: #111111;
    --card-edge: #2c2a28;
    --card-gold: #e2b740;
    --chip-gold: #c9a24a;
    --brand-ink: #5a4a6c;
    --brand-accent: #f2673a;
    --badge-white: #ffffff;
  }
  * { margin: 0; padding: 0; box-sizing: border-box; }
  html, body {
    width: 1200px; height: 900px; overflow: hidden;
    background: var(--page-bg);
  }
  .banner {
    position: absolute; left: 0; top: 50px;
    width: 1200px; height: 800px; overflow: hidden;
    background: var(--photo-deep);
  }
  .banner__photo {
    position: absolute; inset: 0;
    background:
      radial-gradient(ellipse 14% 10% at 52% 40%, rgba(240,182,122,0.55), transparent 75%),
      radial-gradient(ellipse 22% 30% at 68% 62%, rgba(214,140,80,0.75), transparent 75%),
      radial-gradient(ellipse 20% 40% at 18% 30%, rgba(240,182,122,0.6), transparent 72%),
      radial-gradient(ellipse 30% 35% at 40% 85%, rgba(184,112,63,0.7), transparent 75%),
      radial-gradient(ellipse 25% 30% at 92% 45%, rgba(26,16,12,0.85), transparent 80%),
      linear-gradient(100deg, var(--photo-mid) 0%, var(--photo-warm) 22%, var(--photo-mid) 45%, var(--photo-deep) 62%, var(--photo-mid) 75%, var(--photo-dark) 100%);
  }
  .banner__shade {
    position: absolute; inset: 0;
    background: linear-gradient(180deg, rgba(26,16,12,0.35) 0%, transparent 35%, transparent 70%, rgba(26,16,12,0.25) 100%);
  }
  .headline {
    position: absolute; left: 357px; top: 66px;
    font-family: "Montserrat", sans-serif; font-weight: 600;
    font-size: 82px; line-height: 82px; color: var(--text-light);
    letter-spacing: 0.5px;
    text-shadow: 0 2px 10px rgba(0,0,0,0.25);
  }
  .tagline {
    position: absolute; left: 79px; top: 318px;
    font-family: "Open Sans", sans-serif; font-weight: 400;
    font-size: 31px; line-height: 41px; letter-spacing: 2px;
    color: var(--text-light);
    text-shadow: 0 1px 6px rgba(0,0,0,0.3);
  }
  .card {
    position: absolute; border-radius: 16px;
    background: linear-gradient(135deg, var(--card-edge), var(--card-black) 60%);
    box-shadow: 0 10px 24px rgba(0,0,0,0.5);
    font-family: "Open Sans", sans-serif; color: var(--text-light);
  }
  .card--back { left: 40px; top: 535px; width: 300px; height: 190px; transform: rotate(-14deg); }
  .card--front { left: 160px; top: 595px; width: 340px; height: 215px; transform: rotate(-12deg); }
  .card__tier {
    position: absolute; right: 26px; top: 18px;
    color: var(--card-gold); font-size: 24px; font-weight: 600; line-height: 1;
  }
  .card__brand {
    position: absolute; right: 26px; top: 46px;
    color: var(--card-gold); font-size: 14px; font-weight: 400;
  }
  .card__chip {
    position: absolute; left: 52px; top: 92px; width: 38px; height: 30px;
    border-radius: 6px; background: var(--chip-gold);
  }
  .card__number { position: absolute; left: 52px; top: 134px; font-size: 20px; letter-spacing: 1px; }
  .card__holder { position: absolute; left: 52px; top: 172px; font-size: 10px; opacity: 0.8; }
  .card__network {
    position: absolute; right: 30px; top: 132px; width: 30px; height: 30px;
    border-radius: 50%; background: var(--card-gold);
  }
  .brand-badge {
    position: absolute; left: 839px; top: 581px;
    width: 296px; height: 296px; border-radius: 50%;
    background: var(--badge-white);
  }
  .brand-badge__mark {
    position: absolute; left: 118px; top: 62px;
    width: 60px; height: 60px; border-radius: 50%;
    background: var(--brand-accent);
  }
  .brand-badge__name {
    position: absolute; left: 0; right: 0; top: 152px; text-align: center;
    font-family: "Montserrat", sans-serif; font-weight: 600;
    font-size: 34px; line-height: 40px; color: var(--brand-ink);
  }
</style>
</head>
<body>
  <main class="banner">
    <div class="banner__photo" role="img" aria-label="Foto notturna: ragazza di spalle con le braccia alzate in una via cittadina illuminata da luci calde"></div>
    <div class="banner__shade"></div>

    <h1 class="headline">All in One !<br>Una carta per tutti</h1>

    <p class="tagline">Enjoy your cart!<br>Fai quello che vuoi,<br>Nessun limite.<br>Nessun controllo.</p>

    <div class="card card--back">
      <span class="card__tier">Business</span>
      <span class="card__brand">PagoLume</span>
      <span class="card__chip"></span>
      <span class="card__number">1234</span>
      <span class="card__holder">MARCO RIVA</span>
    </div>

    <div class="card card--front">
      <span class="card__tier">Business</span>
      <span class="card__brand">PagoLume</span>
      <span class="card__chip"></span>
      <span class="card__number">1234 5678 9012 3456</span>
      <span class="card__holder">MARCO RIVA</span>
      <span class="card__network"></span>
    </div>

    <div class="brand-badge">
      <span class="brand-badge__mark"></span>
      <span class="brand-badge__name">PagoLume</span>
    </div>
  </main>
</body>
</html>
```